"Every Small Hand Finds Purpose" Teaching Series

16:9 design
Size: 64"x36" @ 300 dpi
Should include the title: Every Small Hand Finds Purpose
and text subtly "Summer 2017"
Should include the church logo in a subtle way.
This artwork will be printed as a large banner but we will also adapt the artwork to be used in other formats like social media, a weekly bulletin, digital signage etc.
We are looking for a graphic that captures the message of the series: God has gifted people with a variety of gifts, abilities and resources to be used in service to Him.
We would like to see designs with bright jewel tones with a modern feel. Attached are examples of designs we like.
Overview of the series: God’s people are diverse: personalities, generations, gifts, abilities, career, resources, skills etc. Many people who are only briefly mentioned in the New Testament had a lasting impact because they used their God given gifts to serve. They opened their home, mentored others, prayed, gave generously, or served in practical ways. God uses all types of people and service for His glory. Some people think that their gifts are small, ordinary or that their work doesn’t matter. This is not the case in God’s eyes. Every person is empowered by God to use his/her gifts to service and that matters for impacting eternity. God has given us all we need to join him in His mission.
Church

```html
<!DOCTYPE html>
<html lang="en">
<head>
<meta charset="utf-8">
<title>Every Small Hand Finds Purpose – Summer 2017</title>
<link href="https://fonts.googleapis.com/css2?family=Montserrat:wght@400;500;800&display=swap" rel="stylesheet">
<style>
  :root {
    --teal: #17a39a;
    --white: #ffffff;
    --umber: #3a2119;
    --rust: #b4542f;
    --sand: #e8b57a;
    --gold: #f2c84b;
    --cocoa: #6b3a2a;
  }
  html, body {
    margin: 0;
    padding: 0;
    width: 1200px;
    height: 676px;
    overflow: hidden;
    background: var(--teal);
  }
  .series-banner {
    display: block;
    width: 1200px;
    height: 676px;
  }
  .series-title {
    font-family: "Montserrat", sans-serif;
    fill: var(--white);
    text-anchor: middle;
  }
  .title-light { font-weight: 500; font-size: 52px; }
  .title-bold { font-weight: 800; font-size: 90px; }
  .title-spaced { font-weight: 400; font-size: 44px; }
  .series-date {
    font-family: "Montserrat", sans-serif;
    font-weight: 400;
    font-size: 36px;
    fill: var(--white);
    text-anchor: middle;
  }
</style>
</head>
<body>
<svg class="series-banner" viewBox="0 0 1200 676" xmlns="http://www.w3.org/2000/svg">
  <defs>
    <linearGradient id="crowd-tones" x1="0" y1="0" x2="1" y2="1">
      <stop offset="0" stop-color="var(--cocoa)"/>
      <stop offset="0.3" stop-color="var(--rust)"/>
      <stop offset="0.5" stop-color="var(--sand)"/>
      <stop offset="0.7" stop-color="var(--umber)"/>
      <stop offset="1" stop-color="var(--rust)"/>
    </linearGradient>
  </defs>

  <rect class="crowd-illustration" role="img"
        aria-label="Illustrated pattern of tall, narrow stylized faces of many skin tones and hair colours on a teal ground"
        x="0" y="0" width="1200" height="676" fill="url(#crowd-tones)"/>

  <g class="cross-emblem" fill="var(--teal)">
    <circle cx="598" cy="329" r="219"/>
    <rect x="140" y="405" width="918" height="47"/>
    <rect x="576" y="530" width="50" height="146"/>
  </g>

  <text class="series-title title-light" x="598" y="262" textLength="380" lengthAdjust="spacingAndGlyphs">EVERY SMALL</text>
  <text class="series-title title-bold" x="598" y="345">HAND</text>
  <text class="series-title title-spaced" x="598" y="392" textLength="392" lengthAdjust="spacing">FINDS PURPOSE</text>
  <text class="series-date" x="598" y="450">SUMMER 2017</text>
</svg>
</body>
</html>
```